New Business Card Design for Manufacturing

We are an engineering/manufacturing company that offers Advanced machining/assembly/engineering services, as well as innovative products for the heavy duty engine cooling markets.

We are looking to get a new business card designed that is clean and modern looking, but still fits the wide range of technical/skilled work we do.

- We hope to use this design as the base for other design work in new Presentations, web, and print work.

Industry/Entity Type

Engineering

Contact Information for Business Card

Our preferred color of blue is (RGB) 22/71/159 but can vary slightly from that color. Our content will be our Logo and full company name (Vantrell Forge Works, Inc.), company address, name, job title, phone number with extension, cell number, fax number, website, and email address on the cards.
We'd like the full company name next to the logo, but we are open to other interpretations of that layout.
Preferably, we would like the back side to be clean with just our logo, and the front to contain all of the contact information.

Colors
2f74b4
0355a3
85abd2

Requirements
Must have
• - Logo, company name, needed content - We are open to interpretation beyond that.
• - Standard size business card.
• - Horizontal orientation.
• - Enough space for lengthy names / job titles (for example, a job title could read "Directory of Human Resources" or "V.P. of Governmental Affairs"). We need this to look clean, whether the title be short (CEO) or long (as described above).

```html
<!DOCTYPE html>
<html lang="en">
<head>
<meta charset="utf-8">
<title>Vantrell Forge Works — Business Card</title>
<link href="https://fonts.googleapis.com/css2?family=Roboto:wght@400;500;700&family=Roboto+Condensed:wght@500&display=swap" rel="stylesheet">
<style>
  :root {
    --page-bg: #e9e7e3;
    --brand-blue: #1151a3;
    --card-white: #f7f7f7;
    --accent-gray: #80878e;
    --back-gray: #7b8187;
    --text-gray: #4d4d4d;
    --white: #ffffff;
  }
  * { margin: 0; padding: 0; box-sizing: border-box; }
  html, body { width: 1200px; height: 960px; overflow: hidden; }
  body {
    background: var(--page-bg);
    font-family: "Roboto", Arial, sans-serif;
    position: relative;
  }
  .card {
    position: absolute;
    width: 600px;
    height: 340px;
    border-radius: 22px;
    overflow: hidden;
    box-shadow: 0 3px 6px rgba(0,0,0,0.35);
  }
  .card-front { left: 302px; top: 130px; background: var(--card-white); }
  .card-back { left: 298px; top: 489px; height: 342px; background: var(--back-gray); }

  .front-sweep { position: absolute; inset: 0; width: 600px; height: 340px; }

  .brand-name {
    position: absolute;
    left: 50px; top: 62px;
    font-weight: 700;
    font-size: 50px;
    letter-spacing: -0.5px;
    color: var(--brand-blue);
    line-height: 1;
  }
  .address {
    position: absolute;
    left: 52px; top: 160px;
    font-size: 14px;
    line-height: 18px;
    color: var(--text-gray);
  }
  .contact-list {
    position: absolute;
    left: 52px; top: 206px;
    list-style: none;
    font-size: 14px;
    color: var(--text-gray);
  }
  .contact-list li {
    display: flex;
    align-items: center;
    height: 19px;
  }
  .contact-list svg { width: 13px; height: 13px; margin-right: 8px; fill: var(--brand-blue); }

  .person {
    position: absolute;
    right: 47px; top: 260px;
    text-align: right;
    color: var(--white);
  }
  .person-name {
    font-family: "Roboto Condensed", "Roboto", Arial, sans-serif;
    font-weight: 500;
    font-size: 25px;
    line-height: 28px;
  }
  .person-title { font-size: 13.5px; line-height: 20px; }

  .back-brand {
    position: absolute;
    inset: 0;
    display: flex;
    align-items: center;
    justify-content: center;
    color: var(--white);
    font-weight: 700;
    font-size: 38px;
    letter-spacing: -0.3px;
  }
</style>
</head>
<body>
  <section class="card card-front">
    <svg class="front-sweep" viewBox="0 0 600 340" aria-hidden="true">
      <path d="M28 340 C 280 318, 500 250, 600 0 L 600 340 Z" fill="var(--accent-gray)"/>
      <path d="M60 340 C 300 318, 505 245, 593 0 L 600 0 L 600 340 Z" fill="var(--white)"/>
      <path d="M66 340 C 310 320, 510 245, 597 0 L 600 0 L 600 340 Z" fill="var(--brand-blue)"/>
    </svg>

    <div class="brand-name">Vantrell</div>

    <p class="address">4120 Halvorsen Road<br>Fairbanks, Alaska 34581</p>

    <ul class="contact-list">
      <li><svg viewBox="0 0 16 16"><path d="M3.6 1.2l2.3 2.6-1.3 1.8c.9 2 2.6 3.7 4.6 4.6l1.8-1.3 2.6 2.3-1.3 2.3C7 13.5 2.5 9 1.5 2.5z"/></svg>612 555 0148</li>
      <li><svg viewBox="0 0 16 16"><path d="M4 0h8a1 1 0 0 1 1 1v14a1 1 0 0 1-1 1H4a1 1 0 0 1-1-1V1a1 1 0 0 1 1-1zm1 2v10h6V2zm3 11a1 1 0 1 0 0 2 1 1 0 0 0 0-2z"/></svg>612 555 0193</li>
      <li><svg viewBox="0 0 16 16"><path d="M1 3h14v1.2L8 9 1 4.2zM1 5.6l7 4.8 7-4.8V13H1z"/></svg>dorian@vantrell.com</li>
      <li><svg viewBox="0 0 16 16"><circle cx="8" cy="8" r="7"/><path d="M4 5c1 0 2 1 2 2s-1 1-1 2 1 2 0 3M10 2.5c-1 1 0 2 1 2.5s1 2 2.5 1.5M9 14c0-1 1-2 2-2" stroke="var(--card-white)" stroke-width="1.2" fill="none"/></svg>www.vantrell.com</li>
    </ul>

    <div class="person">
      <p class="person-name">DORIAN PELL</p>
      <p class="person-title">V.P. of Governmental Affairs</p>
    </div>
  </section>

  <section class="card card-back">
    <div class="back-brand">Vantrell Forge Works, Inc.</div>
  </section>
</body>
</html>
```